Long webpage to explain and sell a complex concept

Accountancy firm wishes to explain Management Accounting to a Small Business audience. We have written the text, assembled a couple of charts and quotes and some concept photos.
There is a lot of text and it is required to explain this type of accounting.
Rather than have a long single block of text which is less likely to be read, we want to break it up with pictures, appropriate white space, diagrams etc. Someone landing on this page will then scroll down reading the text which is designed to keep you reading more.
The page on the website where this will go is https://www.brindlequay.com.au/services/management-accountants-perth/
So the fonts/colours need to fit in. Notice there is a pallet of colours which can be seen here: https://www.brindlequay.com.au/services/

Target Market(s)

Small Business owners in Perth, Western Australia

Number of Pages Required

1 page

Requirements
Must have
• The look and feel needs to match the website indicated in the description above. However we're happy to make the design of this page more interesting than the rest of the site.

```html
<!DOCTYPE html>
<html lang="en">
<head>
<meta charset="utf-8">
<title>Budget Forecasting is the answer</title>
<link rel="stylesheet" href="https://fonts.googleapis.com/css2?family=Open+Sans:wght@300;400&family=Lora:wght@400;700&display=swap">
<style>
  :root {
    --plum: #6e1e6e;
    --ink: #2f2f2f;
    --rule: #8a3a8a;
    --band: #dccab0;
    --band-title: #7a1f2a;
    --paper: #ffffff;
  }
  * { margin: 0; padding: 0; box-sizing: border-box; }
  html, body { width: 1200px; height: 3651px; overflow: hidden; background: var(--paper); }
  .page { position: relative; width: 1200px; height: 3651px; }
  .abs { position: absolute; }

  .title-rule { left: 612px; top: 40px; width: 2px; height: 269px; background: var(--rule); }
  .page-title {
    left: 669px; top: 108px; width: 500px;
    font-family: "Open Sans", sans-serif; font-weight: 300;
    font-size: 53px; line-height: 74px; color: var(--plum);
  }

  .copy {
    font-family: "Lora", serif; font-size: 17.4px; line-height: 38.6px;
    letter-spacing: -0.15px;
    color: var(--ink); text-align: justify;
  }
  .copy strong { font-weight: 700; color: #222; }
  .copy p + p { margin-top: 38px; }
  .fill-last { text-align-last: justify; }

  .photo { border-radius: 1px; }
  .photo-press { left: 27px; top: 421px; width: 560px; height: 356px;
    background: linear-gradient(135deg, #3a3f4a, #6b6f78 45%, #2b3a5c); }
  .photo-office { left: 614px; top: 881px; width: 552px; height: 369px;
    background: linear-gradient(120deg, #7d7f82, #b9b6b0 55%, #e6e2dc); }
  .photo-crystal { left: 30px; top: 1338px; width: 559px; height: 368px;
    background: linear-gradient(135deg, #2a1208, #5e3520 50%, #3a1a0c); }
  .photo-lease { left: 611px; top: 1726px; width: 555px; height: 368px;
    background: linear-gradient(160deg, #4f6e3a, #9bb07a 40%, #c9d3d8 70%, #8f9aa3); }
  .photo-team { left: 30px; top: 2191px; width: 557px; height: 360px;
    background: linear-gradient(110deg, #5b4c45, #a08e80 45%, #e2d2b4 80%, #f3e8cf); }
  .photo-binoculars { left: 614px; top: 2586px; width: 552px; height: 336px;
    background: linear-gradient(180deg, #f7f7f7, #e4e4e4); }
  .photo-summit { left: 38px; top: 2956px; width: 561px; height: 374px;
    background: linear-gradient(180deg, #9fb3c6, #dde6e8 45%, #b7a7a2 75%, #8b7a72); }

  .bullets { list-style: none; }
  .bullets > li { position: relative; padding-left: 41px; }
  .bullets > li::before { content: "\2022"; position: absolute; left: 20px; }
  .sub { list-style: none; }
  .sub li { position: relative; padding-left: 30px; }
  .sub li::before { content: "o"; position: absolute; left: 0; }
  .nowrap { white-space: nowrap; }

  .band { left: 0; top: 3409px; width: 1200px; height: 171px; background: var(--band); text-align: center; }
  .band h2 { font-family: "Lora", serif; font-weight: 400; font-size: 37px; color: var(--band-title); margin-top: 44px; line-height: 44px; }
  .band p { font-family: "Open Sans", sans-serif; font-size: 20px; color: #2a2a2a; margin-top: 6px; }
</style>
</head>
<body>
<main class="page">
  <div class="abs title-rule"></div>
  <h1 class="abs page-title">Budget Forecasting<br>is the answer</h1>

  <div class="abs photo photo-press" role="img" aria-label="Politician speaking at a lectern during a budget announcement"></div>
  <div class="abs copy" style="left:614px; top:366px; width:391px;">
    <p>Now the word <strong>budget</strong> might conjure up a tedious image of boring speeches by politicians, or might feel like a synonym for austerity, but we'd like to convince you that, done right, a Budget Forecast is a fabulous tool to predict your future, lower your stress levels, hold your sales staff to account, and surprisingly, can motivate your staff beyond your expectations. Most importantly, you are <strong>far more likely</strong> to make the profit you want. This is not hyperbole, we are very serious. We see it working all the time.</p>
  </div>

  <div class="abs copy" style="left:196px; top:896px; width:393px;">
    <p style="margin-bottom:26px;">So how does it work?</p>
    <p style="margin-top:0;">At the beginning of a year (if the next financial year is a way off, don't wait, just use any 12 month period, the financial year is just a figment of the tax man's imagination, anyway) take your P&amp;L for the past 12 months, and from that, work out what you plan to spend in the next 12 months.</p>
  </div>
  <div class="abs photo photo-office" role="img" aria-label="Smiling businesswoman working on a laptop in a bright office"></div>

  <div class="abs photo photo-crystal" role="img" aria-label="Fortune teller gazing into a glowing crystal ball"></div>
  <div class="abs copy" style="left:614px; top:1404px; width:391px;">
    <p>"But hold on", we hear you say, "that's just crystal ball gazing". Well yes, some things have to be guessed, but so much is accurately predictable - so much so that <strong>the guessing parts don't actually matter.</strong></p>
  </div>

  <div class="abs copy" style="left:196px; top:1742px; width:393px;">
    <p>Most of the expenses that matter, are probably already locked in. Premises leases, staff wages, financing etc. Goods you only buy when your customers places an order, are a nice problem to have since you've just made a sale to the customer (with hopefully a good margin).</p>
    <p class="fill-last">The real problems are going to be the expenses you're committed to whether or not you have income (sales). Because these</p>
  </div>
  <div class="abs photo photo-lease" role="img" aria-label="For lease signs in front of office buildings"></div>

  <div class="abs photo photo-team" role="img" aria-label="Cheerful team seated at a long table with charts"></div>
  <div class="abs copy" style="left:614px; top:2125px; width:391px;">
    <p>expenses are very predictable you can predict with a great deal of accuracy your expenses for the coming months. You know the profit you want to make (if you don't know, use a minimum like 10% of total income). You can quickly use a spreadsheet to work out how many sales you need to make to cover your expenses and hit your profit target. Simple! You have a plan of how you'd like your year to turn out. (PS make sure you include a proper salary for you over and above the profit).</p>
  </div>

  <div class="abs copy" style="left:196px; top:2660px; width:393px;">
    <p>Now each month you generate a P&amp;L (useful in itself) but which also compares what actually happened to what you planned (known as "budget vs actual").</p>
  </div>
  <div class="abs photo photo-binoculars" role="img" aria-label="Binoculars with budget and actual in the lenses"></div>

  <div class="abs photo photo-summit" role="img" aria-label="Businessman on a mountain top looking through a telescope"></div>
  <div class="abs copy" style="left:619px; top:3008px; width:395px; text-align:left;">
    <p style="text-align:justify; text-align-last:left;">From this you can make two powerful predictions with some simple maths:</p>
    <ul class="bullets">
      <li>How much profit you will make by the<br>end of the year if
        <ul class="sub">
          <li class="nowrap">you hit budget for the rest of the year</li>
          <li>things continue the way they've been going</li>
        </ul>
      </li>
    </ul>
  </div>

  <section class="abs band">
    <h2>The Benefits of Management Reporting</h2>
    <p>The benefits are huge and numerous:</p>
  </section>
</main>
</body>
</html>
```